New Business card design to reflect rebrand

I would like a business card design with a good base colour for our new logo and also a placeholder for a profile pic of the card holder. the design needs to be editable to the point that we can easily change the picture of the person and use that design for printmerlo etc. we are looking at a metalic finish business card so will need a good base colour to bring out the finish.

Target Market(s)

prospective customers

Industry/Entity Type

Business

Contact Information for Business Card

I would like one editable design that we can change the name of the card holder and profile picture. The design need to be in a format that be send to printmerlo etc.

Our address is Fenwick Lodge, Copse Lane, Hartley Wintney, GU14 3TP Tel no. 01483 556172

Requirements
Must have
• place holder for a profile pic for the card holder. in AI or preferably PSD format

```html
<!DOCTYPE html>
<html lang="en">
<head>
<meta charset="UTF-8">
<title>Corvane Workplace Services – Business Card</title>
<link href="https://fonts.googleapis.com/css2?family=Lato:wght@400;700&family=Montserrat:wght@500;600&display=swap" rel="stylesheet">
<style>
  :root {
    --navy: #3f5573;
    --navy-dark: #33465f;
    --orange: #e8600a;
    --white: #ffffff;
    --page: #eceef1;
    --photo-top: #d9dde3;
    --photo-bottom: #8a93a0;
  }
  * { margin: 0; padding: 0; box-sizing: border-box; }
  html, body { width: 1200px; height: 1200px; overflow: hidden; }
  body {
    background: var(--page);
    font-family: 'Lato', Arial, sans-serif;
    position: relative;
  }
  .card {
    position: absolute;
    left: 150px;
    width: 900px;
    height: 514px;
    background: var(--white);
    overflow: hidden;
    box-shadow: 0 6px 22px rgba(0,0,0,0.15);
  }
  .card--front { top: 50px; }
  .card--back { top: 626px; }

  /* Front */
  .front-band-top { position: absolute; left: 0; top: 0; width: 100%; height: 109px; background: var(--navy); }
  .front-band-bottom { position: absolute; left: 0; bottom: 0; width: 100%; height: 109px; background: var(--orange); }
  .brand {
    position: absolute;
    display: flex; align-items: center; gap: 22px;
    color: var(--navy);
    font-family: 'Montserrat', Arial, sans-serif;
    font-weight: 600;
  }
  .brand__dot { border-radius: 50%; background: var(--orange); flex: none; }
  .brand__name { line-height: 1.05; text-transform: uppercase; }
  .brand__name span { display: block; }
  .brand--front { left: 0; right: 0; top: 180px; justify-content: center; }
  .brand--front .brand__dot { width: 74px; height: 74px; }
  .brand--front .brand__main { font-size: 72px; letter-spacing: 2px; }
  .brand--front .brand__sub { font-size: 28px; letter-spacing: 7px; }
  .front-url {
    position: absolute; left: 0; right: 0; bottom: 40px;
    text-align: center; color: var(--white);
    font-weight: 700; font-size: 27px; letter-spacing: 6px;
  }

  /* Back */
  .back-band-mid { position: absolute; left: 0; top: 269px; width: 100%; height: 62px; background: var(--navy); }
  .back-band-bottom { position: absolute; left: 0; top: 331px; width: 100%; height: 183px; background: var(--orange); }
  .brand--back { left: 70px; top: 85px; gap: 16px; }
  .brand--back .brand__dot { width: 54px; height: 54px; }
  .brand--back .brand__main { font-size: 54px; letter-spacing: 1px; }
  .brand--back .brand__sub { font-size: 21px; letter-spacing: 5px; }
  .profile-photo {
    position: absolute; left: 650px; top: 80px; width: 217px; height: 222px;
    border: 3px solid var(--navy-dark); border-radius: 12px;
    background: linear-gradient(180deg, var(--photo-top) 0%, var(--photo-bottom) 100%);
  }
  .address {
    position: absolute; left: 40px; top: 287px;
    display: flex; align-items: center; gap: 18px;
    color: var(--white); font-size: 16px;
  }
  .icon {
    width: 28px; height: 28px; border-radius: 6px;
    display: flex; align-items: center; justify-content: center; flex: none;
  }
  .icon--orange { background: var(--orange); }
  .icon--navy { background: var(--navy); }
  .icon svg { width: 18px; height: 18px; }
  .contact {
    position: absolute;
    display: flex; align-items: center; gap: 16px;
    color: var(--white); font-size: 19px;
  }
  .contact--phone1 { left: 42px; top: 370px; }
  .contact--phone2 { left: 42px; top: 420px; }
  .contact--mail { left: 280px; top: 370px; }
  .contact--web { left: 280px; top: 420px; }
  .holder { position: absolute; right: 34px; top: 366px; text-align: right; color: var(--white); }
  .holder__name { font-size: 27px; font-weight: 700; letter-spacing: 0.5px; }
  .holder__title { font-size: 20px; margin-top: 14px; color: var(--navy-dark); font-weight: 700; }
</style>
</head>
<body>

<section class="card card--front">
  <div class="front-band-top"></div>
  <div class="brand brand--front">
    <div class="brand__dot"></div>
    <div class="brand__name"><span class="brand__main">Corvane</span><span class="brand__sub">Workplace Services</span></div>
  </div>
  <div class="front-band-bottom"></div>
  <p class="front-url">www.website.com</p>
</section>

<section class="card card--back">
  <div class="brand brand--back">
    <div class="brand__dot"></div>
    <div class="brand__name"><span class="brand__main">Corvane</span><span class="brand__sub">Workplace Services</span></div>
  </div>
  <div class="back-band-mid"></div>
  <div class="back-band-bottom"></div>
  <div class="profile-photo" role="img" aria-label="Profile photo of the card holder"></div>

  <div class="address">
    <span class="icon icon--orange">
      <svg viewBox="0 0 24 24"><path d="M12 2a7 7 0 0 0-7 7c0 5 7 13 7 13s7-8 7-13a7 7 0 0 0-7-7zm0 9.5A2.5 2.5 0 1 1 12 6.5a2.5 2.5 0 0 1 0 5z" fill="#fff"/></svg>
    </span>
    <span>Address: Street No, Nord Avenue, Co,City/State Zipcode</span>
  </div>

  <div class="contact contact--phone1">
    <span class="icon icon--navy">
      <svg viewBox="0 0 24 24"><rect x="7" y="3" width="10" height="18" rx="2" fill="none" stroke="#fff" stroke-width="2"/><line x1="11" y1="18" x2="13" y2="18" stroke="#fff" stroke-width="2"/></svg>
    </span>
    <span>+ 000 - 000 - 000</span>
  </div>
  <div class="contact contact--phone2">
    <span class="icon icon--navy">
      <svg viewBox="0 0 24 24"><path d="M6.6 10.8a15 15 0 0 0 6.6 6.6l2.2-2.2a1 1 0 0 1 1-.25 11 11 0 0 0 3.6.6 1 1 0 0 1 1 1V20a1 1 0 0 1-1 1A17 17 0 0 1 3 4a1 1 0 0 1 1-1h3.5a1 1 0 0 1 1 1 11 11 0 0 0 .6 3.6 1 1 0 0 1-.25 1z" fill="#fff"/></svg>
    </span>
    <span>+ 000 - 000 - 000</span>
  </div>
  <div class="contact contact--mail">
    <span class="icon icon--navy">
      <svg viewBox="0 0 24 24"><rect x="3" y="6" width="18" height="12" rx="1.5" fill="none" stroke="#fff" stroke-width="2"/><path d="M3.5 7l8.5 6 8.5-6" fill="none" stroke="#fff" stroke-width="2"/></svg>
    </span>
    <span>mail@website.com</span>
  </div>
  <div class="contact contact--web">
    <span class="icon icon--navy">
      <svg viewBox="0 0 24 24" fill="none" stroke="#fff" stroke-width="1.6"><circle cx="12" cy="12" r="9"/><ellipse cx="12" cy="12" rx="4" ry="9"/><line x1="3" y1="12" x2="21" y2="12"/><line x1="5" y1="7.5" x2="19" y2="7.5"/><line x1="5" y1="16.5" x2="19" y2="16.5"/></svg>
    </span>
    <span>www.website.com</span>
  </div>

  <div class="holder">
    <p class="holder__name">CARD HOLDER NAME</p>
    <p class="holder__title">JOB TITLE/POSITION</p>
  </div>
</section>

</body>
</html>
```